Marrowby Water Taxi and Transport Business Card

I need business cards for my new water taxi and freight transport business I have started here in Kodiak Alaska. Kodiak is a remote island in the middle of the gulf of Alaska. There are seven native villages around the island and Kodiak is the #2 fishing port in the United States. We also have the largest Coast Guard Base in the U.S. My company will be providing water taxi and freight transport logistics to the villages and many hunting and fishing lodges as well as remote properties around the island.

I would like a business card that isn't status quo, something that stands out, either in feel or appearance. I do like clean minimal designs but it needs to have the necessary contact info on it.

Target Market(s)

remote lodge / property owners, residents of the many villages around Kodiak and any one wanting to enjoy the great outdoors of Kodiak Alaska

Industry/Entity Type

Business

Contact Information for Business Card

I like clean simple designs that aren't cluttered but still provide the necessary information

Colors
0255a3
3277b5
33a4d5
9bcb3c
add136
fbed22
ffc214
f78f20
f37122

Requirements
Must have
• logo and contact info
• Captain Mason Elwick
• www.marrowbyferryline.com
• mason@marrowbyferryline.com

```html
<!DOCTYPE html>
<html lang="en">
<head>
<meta charset="utf-8">
<title>Marrowby Water Taxi and Transport – Business Card</title>
<link href="https://fonts.googleapis.com/css2?family=Open+Sans:wght@400;600;700&display=swap" rel="stylesheet">
<style>
  :root{
    --navy:#0255a3;
    --mid-blue:#3277b5;
    --sky:#33a4d5;
    --pale-sky:#bfe3f4;
    --sun:#f7a21f;
    --paper:#ffffff;
    --ink:#1d4f8f;
    --backdrop:#e9ecef;
    --back-top:#1f79d0;
    --back-bottom:#0a3f8c;
  }
  *{box-sizing:border-box;margin:0;padding:0}
  html,body{width:1200px;height:913px;overflow:hidden}
  body{
    background:var(--backdrop);
    font-family:"Open Sans",Arial,sans-serif;
    display:flex;align-items:center;justify-content:center;gap:60px;
  }
  .card{
    position:relative;width:525px;height:300px;border-radius:18px;overflow:hidden;
    box-shadow:0 14px 30px rgba(0,0,0,.18);
  }
  /* Front */
  .card--front{background:var(--paper)}
  .front__sun{
    position:absolute;right:-22px;top:22px;width:44px;height:44px;border-radius:50%;background:var(--sun);
  }
  .front__boat-art{
    position:absolute;left:190px;top:40px;width:220px;height:120px;border-radius:10px;
    background:linear-gradient(180deg,rgba(200,205,212,.25),rgba(200,205,212,.08));
  }
  .front__logo-art{
    position:absolute;left:36px;top:70px;width:110px;height:70px;border-radius:8px;
    background:linear-gradient(180deg,var(--pale-sky),var(--sky));
  }
  .brand{
    position:absolute;left:36px;top:150px;color:var(--navy);
  }
  .brand__name{font-weight:700;font-size:40px;letter-spacing:1px;line-height:1}
  .brand__tagline{font-weight:700;font-size:14px;margin-top:4px;color:var(--navy)}
  .contact{position:absolute;right:30px;top:44px;text-align:right;color:var(--ink)}
  .contact__name{font-weight:700;font-size:19px;color:var(--mid-blue);margin-bottom:10px}
  .contact__line{display:flex;justify-content:flex-end;align-items:center;gap:7px;font-size:12.5px;line-height:1.55}
  .contact__line svg{width:12px;height:12px;flex:none}
  .front__rule{position:absolute;left:36px;right:30px;top:130px;height:1px;background:var(--mid-blue);opacity:.6}
  .front__rule--low{top:236px;right:230px}
  .front__waves{position:absolute;left:0;bottom:0;width:100%;height:130px}
  /* Back */
  .card--back{background:linear-gradient(160deg,var(--back-top),var(--back-bottom))}
  .back__mark{
    position:absolute;inset:0;display:flex;align-items:center;justify-content:center;gap:14px;
    color:var(--paper);font-weight:700;font-size:36px;letter-spacing:1px;
  }
  .back__dot{width:34px;height:34px;border-radius:50%;background:var(--sun)}
</style>
</head>
<body>
  <section class="card card--front" aria-label="Business card front">
    <div class="front__boat-art" role="img" aria-label="Faint boat illustration"></div>
    <div class="front__sun"></div>
    <div class="front__logo-art" role="img" aria-label="Mountain, sun and boat illustration"></div>
    <div class="front__rule"></div>
    <div class="brand">
      <div class="brand__name">MARROWBY</div>
      <div class="brand__tagline">Water Taxi &amp; Transport</div>
    </div>
    <div class="contact">
      <div class="contact__name">Captain Mason Elwick</div>
      <div class="contact__line">mason@marrowbyferryline.com
        <svg viewBox="0 0 12 12"><rect x="1" y="2.5" width="10" height="7" fill="none" stroke="#3277b5" stroke-width="1"/><path d="M1 2.5 6 7l5-4.5" fill="none" stroke="#3277b5" stroke-width="1"/></svg>
      </div>
      <div class="contact__line">www.marrowbyferryline.com
        <svg viewBox="0 0 12 12"><circle cx="6" cy="6" r="5" fill="none" stroke="#3277b5" stroke-width="1"/><ellipse cx="6" cy="6" rx="2.2" ry="5" fill="none" stroke="#3277b5" stroke-width="1"/><path d="M1 6h10" stroke="#3277b5" stroke-width="1"/></svg>
      </div>
    </div>
    <div class="front__rule front__rule--low"></div>
    <svg class="front__waves" viewBox="0 0 525 130" preserveAspectRatio="none" aria-hidden="true">
      <path d="M0 110 C120 100 240 60 340 60 C420 60 470 20 525 10 L525 130 L0 130Z" fill="#bfe3f4"/>
      <path d="M0 120 C140 112 260 80 360 78 C440 76 490 40 525 32 L525 130 L0 130Z" fill="#33a4d5"/>
      <path d="M0 126 C160 122 280 100 380 98 C450 96 500 70 525 62 L525 130 L0 130Z" fill="#0255a3"/>
    </svg>
  </section>

  <section class="card card--back" aria-label="Business card back">
    <div class="back__mark"><span class="back__dot"></span>Marrowby</div>
  </section>
</body>
</html>
```